Ashwell Court Apartments
stationary
Project: Ashwell Court Apartments
Ashwell Court Apartments - Real Estate
Creative Brief
Traditional
Daniel Kessing
2430 Ashwell Court Houston TX 77091
dpkessing@mailvora.net

```html
<!DOCTYPE html>
<html lang="en">
<head>
<meta charset="utf-8">
<title>Ashwell Court Apartments – Business Card</title>
<link rel="stylesheet" href="https://fonts.googleapis.com/css2?family=Cinzel:wght@500&family=Crimson+Text&display=swap">
<style>
  :root {
    --green: #2f8a3f;
    --black: #141414;
    --white: #ffffff;
    --stage: #e6e8e6;
  }
  * { box-sizing: border-box; margin: 0; padding: 0; }
  html, body {
    width: 1200px;
    height: 1009px;
    overflow: hidden;
    background: var(--stage);
  }
  .sheet {
    width: 1200px;
    height: 1009px;
    display: flex;
    flex-direction: column;
    align-items: center;
    justify-content: center;
    gap: 48px;
  }
  .card {
    position: relative;
    width: 760px;
    height: 434px;
    border-radius: 26px;
    overflow: hidden;
    box-shadow: 0 6px 18px rgba(0,0,0,0.18);
  }

  /* Back */
  .card-back {
    background: var(--green);
    display: flex;
    align-items: center;
    justify-content: center;
  }
  .brand {
    display: flex;
    align-items: center;
    gap: 18px;
    font-family: 'Cinzel', serif;
    font-weight: 500;
    line-height: 1.05;
    text-transform: uppercase;
  }
  .brand-mark {
    flex: none;
    border-radius: 50%;
  }
  .card-back .brand { color: var(--white); }
  .card-back .brand-mark { width: 64px; height: 64px; background: var(--white); }
  .card-back .brand-name { font-size: 44px; letter-spacing: 2px; }
  .card-back .brand-sub { display: block; font-size: 22px; letter-spacing: 9px; margin-top: 6px; }

  /* Front */
  .card-front { background: var(--white); }
  .front-waves {
    position: absolute;
    inset: 0;
    width: 100%;
    height: 100%;
  }
  .card-front .brand {
    position: absolute;
    left: 44px;
    top: 48px;
    color: var(--green);
    gap: 14px;
  }
  .card-front .brand-mark { width: 44px; height: 44px; background: var(--green); }
  .card-front .brand-name { font-size: 30px; letter-spacing: 1px; }
  .card-front .brand-sub { display: block; font-size: 15px; letter-spacing: 6px; margin-top: 4px; }

  .holder {
    position: absolute;
    right: 52px;
    top: 140px;
    font-family: 'Cinzel', serif;
    font-weight: 500;
    font-size: 24px;
    letter-spacing: 1.5px;
    color: var(--green);
    text-transform: uppercase;
  }
  .contact {
    position: absolute;
    right: 52px;
    bottom: 28px;
    text-align: right;
    font-family: 'Crimson Text', serif;
    font-size: 20px;
    line-height: 1.25;
    color: var(--white);
    font-style: normal;
  }
  .contact .gap { display: block; height: 10px; }
</style>
</head>
<body>
<main class="sheet">

  <section class="card card-back" aria-label="Card back">
    <div class="brand">
      <span class="brand-mark"></span>
      <span class="brand-name">Ashwell Court<span class="brand-sub">Apartments</span></span>
    </div>
  </section>

  <section class="card card-front" aria-label="Card front">
    <svg class="front-waves" viewBox="0 0 760 434" preserveAspectRatio="none" aria-hidden="true">
      <path d="M0 178 C 180 165, 320 225, 470 240 C 600 252, 700 230, 760 205 L760 434 L0 434 Z" fill="var(--black)"/>
      <path d="M0 198 C 180 187, 320 248, 470 262 C 600 274, 700 254, 760 228 L760 434 L0 434 Z" fill="var(--white)"/>
      <path d="M0 210 C 180 200, 320 260, 470 272 C 600 282, 700 264, 760 240 L760 434 L0 434 Z" fill="var(--green)"/>
    </svg>

    <div class="brand">
      <span class="brand-mark"></span>
      <span class="brand-name">Ashwell Court<span class="brand-sub">Apartments</span></span>
    </div>

    <p class="holder">Daniel Kessing</p>

    <address class="contact">
      2430 Ashwell Court<br>
      Houston TX 77091
      <span class="gap"></span>
      713-555-0184<br>
      dpkessing@mailvora.net
    </address>
  </section>

</main>
</body>
</html>
```